Redesign of Form/Document Navigation Page

I need a redesign of our document and navigation bar on the left. We want the same navigation bar layout/setup but want the buttons and typography to be simple and matching all over. The form needs to be aesthetically pleasing and fit within the page.

1st attachment is our Direct Deposit and the second is the form continued.

```html
<!DOCTYPE html>
<html lang="en">
<head>
<meta charset="UTF-8">
<title>Direct Deposit Authorization – Northgate Patrol Co.</title>
<link rel="stylesheet" href="https://fonts.googleapis.com/css2?family=Open+Sans:wght@400;600;700&display=swap">
<style>
  :root {
    --brand-blue: #1f56a8;
    --brand-blue-dark: #245a9a;
    --page-bg: #f0f0ec;
    --panel-bg: #ffffff;
    --border: #dcdcd8;
    --input-border: #c9c9c9;
    --text: #333333;
    --text-muted: #444444;
    --white: #ffffff;
  }
  * { box-sizing: border-box; margin: 0; padding: 0; }
  html, body { width: 1200px; height: 1138px; overflow: hidden; }
  body {
    position: relative;
    background: var(--page-bg);
    font-family: "Open Sans", Arial, sans-serif;
    color: var(--text);
  }

  /* Header */
  .site-header {
    position: absolute; left: 0; top: 0; width: 1200px; height: 96px;
    background: var(--white); border-bottom: 1px solid var(--border);
  }
  .brand { position: absolute; left: 36px; top: 29px; display: flex; align-items: center; gap: 10px; }
  .brand-mark { width: 34px; height: 34px; border-radius: 50%; background: var(--brand-blue); }
  .brand-name { color: var(--brand-blue); font-weight: 600; font-size: 21px; line-height: 34px; }
  .top-nav { position: absolute; left: 362px; top: 39px; font-size: 12.5px; color: var(--text); }
  .top-nav a { color: var(--text); text-decoration: none; }
  .top-nav .sep { margin: 0 11px; }
  .user-menu { position: absolute; right: 37px; top: 37px; display: flex; align-items: center; gap: 8px; font-size: 12.5px; color: #555; letter-spacing: 0.3px; }

  .back-link {
    position: absolute; left: 35px; top: 118px; font-size: 15px; color: var(--brand-blue);
    text-decoration: none; display: flex; align-items: center; gap: 4px;
  }

  /* Sidebar */
  .side-nav { position: absolute; left: 35px; top: 151px; width: 251px; }
  .side-item {
    height: 79px; margin-bottom: 6.3px; background: var(--white); border: 1px solid var(--border);
    display: flex; align-items: center; padding-left: 15px; gap: 10px;
    font-size: 15px; color: var(--text); letter-spacing: 0.3px;
  }
  .side-icon {
    width: 47px; height: 47px; border-radius: 50%; background: var(--brand-blue);
    display: flex; align-items: center; justify-content: center; flex: none;
  }

  /* Main panel */
  .doc-panel {
    position: absolute; left: 308px; top: 151px; width: 856px; height: 805px;
    background: var(--panel-bg); border: 1px solid var(--border);
  }
  .doc-title {
    position: absolute; left: 26px; top: 47px; font-size: 18.5px; font-weight: 600;
    color: var(--brand-blue); letter-spacing: 0.1px; white-space: nowrap;
  }
  .doc-title-rule { position: absolute; left: 28px; top: 81px; width: 114px; height: 2px; background: var(--brand-blue); }
  .doc-body { position: absolute; left: 28px; top: 98px; width: 800px; font-size: 10.2px; line-height: 20px; color: var(--text-muted); }
  .doc-body p + p { margin-top: 7px; }

  .section-label { position: absolute; font-size: 14px; font-weight: 600; color: var(--brand-blue); }
  .field-label { position: absolute; font-size: 13px; color: var(--text); }
  .text-input { position: absolute; height: 34px; background: var(--white); border: 1px solid var(--input-border); }
  .btn {
    position: absolute; background: var(--brand-blue); color: var(--white); font-weight: 600;
    display: flex; align-items: center; justify-content: center; font-size: 14px;
  }
  .manager-title { position: absolute; left: 26px; top: 450px; font-size: 18.5px; font-weight: 600; color: var(--brand-blue); letter-spacing: 0.2px; }
  .manager-box {
    position: absolute; left: 28px; top: 488px; width: 797px; height: 267px;
    background: var(--page-bg); border: 1px solid var(--border);
  }

  /* Footer */
  .site-footer {
    position: absolute; left: 0; top: 1012px; width: 1200px; height: 126px;
    background: var(--brand-blue); color: var(--white); text-align: center;
  }
  .social { position: absolute; left: 0; width: 100%; top: 26px; display: flex; justify-content: center; gap: 12px; }
  .social span { width: 22px; height: 22px; border-radius: 3px; background: var(--white); }
  .copyright { position: absolute; top: 70px; width: 100%; font-size: 11.8px; }
  .footer-links { position: absolute; top: 94px; width: 100%; font-size: 11.8px; }
</style>
</head>
<body>

<header class="site-header">
  <div class="brand">
    <div class="brand-mark"></div>
    <div class="brand-name">Northgate Patrol Co.</div>
  </div>
  <nav class="top-nav"><a href="#">Home</a><span class="sep">|</span><a href="#">Help</a></nav>
  <div class="user-menu">DANA MILLER
    <svg width="21" height="21" viewBox="0 0 21 21"><circle cx="10.5" cy="10.5" r="10.5" fill="#555"/><path d="M7.2 7.2a4.8 4.8 0 1 0 6.6 0" stroke="#fff" stroke-width="1.8" fill="none" stroke-linecap="round"/><line x1="10.5" y1="4.8" x2="10.5" y2="10.2" stroke="#fff" stroke-width="1.8" stroke-linecap="round"/></svg>
  </div>
</header>

<a class="back-link" href="#"><svg width="14" height="12" viewBox="0 0 14 12"><path d="M7 0v12L0 6zM14 0v12L7 6z" fill="#1f56a8"/></svg>Back To Profile</a>

<nav class="side-nav">
  <div class="side-item"><span class="side-icon"><svg width="20" height="20" viewBox="0 0 20 20"><path d="M2 3v6l9 9 7-7-9-9H3z" fill="#fff"/><circle cx="5.5" cy="6" r="1.4" fill="#1f56a8"/></svg></span>Direct Deposit</div>
  <div class="side-item"><span class="side-icon"><svg width="20" height="20" viewBox="0 0 20 20"><path d="M4 9a6 6 0 0 1 11-3" stroke="#fff" stroke-width="2.4" fill="none"/><path d="M16 2v5h-5z" fill="#fff"/><path d="M16 11a6 6 0 0 1-11 3" stroke="#fff" stroke-width="2.4" fill="none"/><path d="M4 18v-5h5z" fill="#fff"/></svg></span>Change W-4</div>
  <div class="side-item"><span class="side-icon"><svg width="18" height="18" viewBox="0 0 18 18" fill="none" stroke="#fff" stroke-width="2"><rect x="1" y="1" width="6" height="6"/><rect x="11" y="1" width="6" height="6"/><rect x="1" y="11" width="6" height="6"/><rect x="11" y="11" width="6" height="6"/></svg></span>Labour Code</div>
  <div class="side-item"><span class="side-icon"><svg width="18" height="18" viewBox="0 0 18 18"><circle cx="9" cy="5" r="4" fill="#fff"/><path d="M1 18c0-5 3.5-7.5 8-7.5s8 2.5 8 7.5z" fill="#fff"/></svg></span>Personal Information</div>
  <div class="side-item"><span class="side-icon"><svg width="22" height="20" viewBox="0 0 22 20"><ellipse cx="8" cy="8" rx="7.5" ry="6" fill="#fff"/><ellipse cx="14.5" cy="12.5" rx="6.5" ry="5.2" fill="#fff" stroke="#1f56a8" stroke-width="1.2"/></svg></span>Appraisal and Review</div>
  <div class="side-item"><span class="side-icon"><svg width="18" height="18" viewBox="0 0 18 18"><path d="M3 15l1-4 9-9 3 3-9 9z" fill="#fff"/></svg></span>Write Up-Slip</div>
  <div class="side-item"><span class="side-icon"><svg width="20" height="18" viewBox="0 0 20 18" fill="none" stroke="#fff" stroke-width="2"><path d="M2 1v15h17"/><path d="M4 13l4-5 3 3 6-6"/></svg></span>Employee Performance</div>
</nav>

<main class="doc-panel">
  <h1 class="doc-title">IMPORTANT! PLEASE READ AND SIGN BEFORE COMPLETING AND SUBMITTING.</h1>
  <div class="doc-title-rule"></div>
  <div class="doc-body">
    <p>I hereby authorize NORTHGATE PATROL CO. to deposit any amounts owed me, as instructed by my employer, by initiating credit entries to my account at the financial institution (hereinafter "Bank") indicated on this form. Further. I authorize Bank to accept and to credit any credit entries indicated by NORTHGATE PATROL CO. to my account. In the even that NORTHGATE PATROL CO. deposits funds erroneously into my account. I authorize NORTHGATE PATROL CO. to debit my account for an amount not to exceed the original amount of the erroneous credit.</p>
    <p>This authorization is to remain in full force and effect until NORTHGATE PATROL CO. and Bank have received written notice from me of its termination in such time and in such manner as to afford NORTHGATE PATROL CO. and Bank reasonable opportunity to act on it.</p>
  </div>

  <div class="section-label" style="left:28px; top:265px;">EMPLOYEE NAME:</div>
  <div class="field-label" style="left:29px; top:306px;">Employee Signature</div>
  <div class="field-label" style="left:284px; top:306px;">Sign Date</div>
  <div class="text-input" style="left:30px; top:333px; width:235px;"></div>
  <div class="text-input" style="left:285px; top:333px; width:235px;"></div>
  <div class="btn" style="left:28px; top:390px; width:155px; height:33px;">Accept Document</div>

  <h2 class="manager-title">ONLY PAYROLL MANAGER SIGNS BELOW</h2>
  <section class="manager-box">
    <div class="field-label" style="left:27px; top:30px;">Company Name:</div>
    <div class="field-label" style="left:405px; top:30px;">Employee File Number:</div>
    <div class="text-input" style="left:28px; top:57px; width:364px;"></div>
    <div class="text-input" style="left:406px; top:57px; width:364px;"></div>
    <div class="field-label" style="left:27px; top:102px;">Comments:</div>
    <div class="text-input" style="left:28px; top:129px; width:741px; height:65px;"></div>
    <div class="btn" style="left:28px; top:210px; width:84px; height:34px; font-size:13px; background:var(--brand-blue-dark);">SUBMIT</div>
  </section>
</main>

<footer class="site-footer">
  <div class="social" role="img" aria-label="Social network links">
    <span></span><span></span><span></span><span></span><span></span>
  </div>
  <div class="copyright">Copyright @ 2015 - 2016 Northgate Patrol Co. All Rights Reserved.</div>
  <div class="footer-links">Privacy Policy / About / Contact Us</div>
</footer>

</body>
</html>
```